Hartwell Estates Business Cards

I would like a business card that includes myself and my partner.
Includes: Logo, office #, email, website, our names, our numbers and possibly the address. I would also like the logo to be embossed and the card to be horizontal.
There is a photo of our yard signs to give you an idea of the colors of our business.

Target Market(s)

Everyone in real estate market.
We are in a rural area. Our clientele are from all socioeconomic backgrounds.

Industry/Entity Type

Real Estate Agent

Contact Information for Business Card

Company Name: Hartwell Estates
Our Names, Titles & Cell #'s : Dana Pembrook-Broker (555).317.6624, Marla Pembrook-Realtor (555).609.1385
Office #: (555).240.3918
Website: hartwellestates-demo.com
Joint Email: pembrook@hartwellestates-demo.com
Office Address: 418B W. Calloway Ave.
Linden Creek, LA. 70913

Font styles to use
Serif

Requirements
Must have
• HORIZONTAL, Logo, Myself and my partners names, Our cell #'s, our office #, our website, our email address
Nice to have
• Embossed logo, office address, our titles.

```html
<!DOCTYPE html>
<html lang="en">
<head>
<meta charset="utf-8">
<title>Hartwell Estates Business Cards</title>
<link rel="stylesheet" href="https://fonts.googleapis.com/css2?family=PT+Sans:wght@400;700&display=swap">
<style>
  :root {
    --stage: #e9e6e2;
    --card-black: #0e0d10;
    --brand-purple: #4c2870;
    --name-purple: #6b3b98;
    --swoosh-white: #e4e4e6;
    --text-light: #f2f2f2;
  }
  * { margin: 0; padding: 0; box-sizing: border-box; }
  html, body { width: 1200px; height: 900px; overflow: hidden; }
  body {
    background: var(--stage);
    font-family: "PT Sans", Arial, sans-serif;
    position: relative;
  }
  .card {
    position: absolute;
    width: 520px;
    height: 297px;
    background: radial-gradient(ellipse at 40% 35%, #1c1b20 0%, var(--card-black) 70%);
    overflow: hidden;
    box-shadow: 0 6px 18px rgba(0,0,0,0.25);
  }
  .card-front { left: 80px; top: 150px; }
  .card-back { left: 600px; top: 453px; }

  .front-brand {
    position: absolute;
    inset: 0;
    display: flex;
    align-items: center;
    justify-content: center;
    gap: 16px;
  }
  .brand-dot {
    width: 44px; height: 44px;
    border-radius: 50%;
    background: var(--brand-purple);
  }
  .brand-name {
    font-family: "PT Sans", Arial, sans-serif;
    font-weight: 700;
    color: var(--brand-purple);
    font-size: 44px;
    letter-spacing: 1px;
    line-height: 1;
  }

  .back-art { position: absolute; inset: 0; }
  .back-brand {
    position: absolute;
    right: 34px; top: 42px;
    font-family: "PT Sans", Arial, sans-serif;
    font-weight: 700;
    color: var(--brand-purple);
    font-size: 26px;
    line-height: 1;
  }
  .contacts {
    position: absolute;
    left: 36px; top: 22px;
    color: var(--text-light);
  }
  .agent { margin-bottom: 6px; }
  .agent-name {
    color: var(--name-purple);
    font-weight: 700;
    font-size: 19px;
    line-height: 1.15;
  }
  .agent-title, .agent-phone { font-size: 14px; line-height: 1.3; padding-left: 6px; }
  .office-lines { list-style: none; margin-top: 2px; }
  .office-lines li {
    display: flex; align-items: center; gap: 7px;
    font-size: 14.5px; line-height: 1.35;
  }
  .office-lines svg { width: 11px; height: 11px; flex: none; }
  .address {
    position: absolute;
    right: 22px; bottom: 52px;
    text-align: right;
    color: var(--text-light);
    font-size: 11.5px;
    line-height: 1.4;
  }
</style>
</head>
<body>
  <section class="card card-front" aria-label="Card front">
    <div class="front-brand">
      <span class="brand-dot"></span>
      <span class="brand-name">Hartwell Estates</span>
    </div>
  </section>

  <section class="card card-back" aria-label="Card back">
    <svg class="back-art" viewBox="0 0 520 297" preserveAspectRatio="none">
      <path d="M0,236 C150,270 330,246 460,170 C340,254 150,278 0,272 Z" fill="var(--swoosh-white)"/>
      <path d="M0,268 C170,276 340,250 520,146 L520,297 L0,297 Z" fill="#000"/>
      <path d="M0,272 C175,278 345,254 520,152 L520,297 L0,297 Z" fill="var(--brand-purple)"/>
    </svg>
    <div class="back-brand">Hartwell Estates</div>

    <div class="contacts">
      <div class="agent">
        <div class="agent-name">Dana Pembrook</div>
        <div class="agent-title">Broker</div>
        <div class="agent-phone">(555).317.6624</div>
      </div>
      <div class="agent">
        <div class="agent-name">Marla Pembrook</div>
        <div class="agent-title">Realtor</div>
        <div class="agent-phone">(555).609.1385</div>
      </div>
      <ul class="office-lines">
        <li>
          <svg viewBox="0 0 12 12"><path d="M1,4 Q6,0 11,4 L9,5.5 L8,4 L4,4 L3,5.5 Z M3,6 L9,6 L10,11 L2,11 Z" fill="var(--brand-purple)"/></svg>
          (555).240.3918
        </li>
        <li>
          <svg viewBox="0 0 12 12"><circle cx="6" cy="6" r="5.5" fill="var(--brand-purple)"/><path d="M0.5,6 H11.5 M6,0.5 V11.5" stroke="var(--card-black)" stroke-width="0.8"/></svg>
          hartwellestates-demo.com
        </li>
        <li>
          <svg viewBox="0 0 12 12"><rect x="0.5" y="2" width="11" height="8" fill="var(--brand-purple)"/><path d="M0.5,2 L6,6.5 L11.5,2" fill="none" stroke="var(--card-black)" stroke-width="0.8"/></svg>
          pembrook@hartwellestates-demo.com
        </li>
      </ul>
    </div>

    <div class="address">418B W. Calloway<br>Ave. Linden Creek, LA. 70913</div>
  </section>
</body>
</html>
```